Business Card for Multi-Brand Sportswear Company

We are looking for a business card which represents our company and the multiple brands within it.

The company: Fen Athletics (LTD)
The brands: Fen, TavaPuni, ElmStretch, Grit and Rain

Employees using these cards would be representing Fen Athletics, rather than any of the individual brands. You will see a current design within the uploaded files, to give some inspiration. The actual text of the brands is not necessary, but the logos should be on there is some format.

Our creative minds on this are stretched, so we are looking for someone to make this their own, and show us what a good business card should look like.

We may like to get these printed with spot gloss, so keep that in mind with your designs.

www.fenathletics.co.uk

Industry/Entity Type

Business

Contact Information for Business Card

Leo Pemberton-Hale
Operations Manager
(+44) 1632 960 418
Leo@fenathletics.co.uk
www.fenathletics.co.uk

Font styles to use
Sans Serif
Other font styles liked:
• Eurostile

Colors
ffffff

Requirements
Nice to have
• Dark (black) background

```html
<!DOCTYPE html>
<html lang="en">
<head>
<meta charset="utf-8">
<title>Fen Athletics – Business Card</title>
<link rel="stylesheet" href="https://fonts.googleapis.com/css2?family=Saira:wght@400;500;600&display=swap">
<style>
  :root{
    --bg:#3a322d;
    --card:#1d1e21;
    --card-edge:#26272b;
    --white:#ffffff;
    --grey:#c9cacd;
    --muted:#6d6e73;
    --violet:#8a7aa3;
    --red:#e0232e;
  }
  *{box-sizing:border-box;margin:0;padding:0}
  html,body{width:1200px;height:769px;overflow:hidden;background:var(--bg);font-family:"Saira",Arial,sans-serif}
  .stage{position:relative;width:1200px;height:769px}
  .card{position:absolute;top:224px;width:520px;height:320px;background:var(--card);border:1px solid var(--card-edge);box-shadow:0 12px 30px rgba(0,0,0,.45)}
  .card--front{left:50px}
  .card--back{left:630px}

  .wordmark{position:absolute;color:var(--white);font-weight:600;letter-spacing:.02em;line-height:1;white-space:nowrap}
  .wordmark__tag{display:block;margin-top:6px;font-weight:400;font-size:8px;letter-spacing:.28em;color:var(--grey)}
  .card--front .wordmark{top:46px;right:44px;font-size:34px;text-align:right}

  .contact{position:absolute;left:40px;bottom:36px}
  .contact__name{color:var(--red);font-size:20px;font-weight:500;letter-spacing:.02em;text-transform:uppercase;line-height:1.1}
  .contact__role{color:var(--grey);font-size:13px;margin-bottom:10px}
  .contact__row{display:flex;align-items:center;gap:9px;color:var(--grey);font-size:12.5px;line-height:1.55}
  .contact__row svg{width:11px;height:11px;fill:var(--red);flex:none}
  .contact__address{color:var(--grey);font-size:12.5px;margin-top:8px}

  .card--back .wordmark{top:92px;left:0;right:0;text-align:center;font-size:48px}
  .card--back .wordmark__tag{font-size:10px;margin-top:9px}
  .brands{position:absolute;left:34px;right:34px;bottom:34px;display:flex;justify-content:space-between;align-items:center}
  .brand{display:flex;align-items:center;gap:7px;font-size:13px;font-weight:500;letter-spacing:.04em;white-space:nowrap}
  .brand__dot{width:9px;height:9px;border-radius:50%;border:1.5px solid currentColor}
  .brand__square{width:10px;height:10px;background:currentColor}
  .brand--fen{color:var(--white)}
  .brand--tava{color:var(--muted)}
  .brand--elm{color:var(--violet)}
  .brand--grit{color:var(--red)}
</style>
</head>
<body>
<main class="stage">
  <section class="card card--front" aria-label="Business card front">
    <div class="wordmark">Fen Athletics<span class="wordmark__tag">PERFORMANCE WEAR</span></div>
    <div class="contact">
      <p class="contact__name">Leo Pemberton-Hale</p>
      <p class="contact__role">Operations Manager</p>
      <p class="contact__row"><svg viewBox="0 0 24 24" aria-hidden="true"><path d="M6.6 10.8a15 15 0 0 0 6.6 6.6l2.2-2.2c.3-.3.7-.4 1-.2 1.1.4 2.3.6 3.6.6.6 0 1 .4 1 1V20c0 .6-.4 1-1 1A17 17 0 0 1 3 4c0-.6.4-1 1-1h3.5c.6 0 1 .4 1 1 0 1.3.2 2.5.6 3.6.1.3 0 .7-.2 1z"/></svg>(+44) 1632 960 418</p>
      <p class="contact__row"><svg viewBox="0 0 24 24" aria-hidden="true"><path d="M2 5h20v14H2zM4 7v.5l8 5 8-5V7l-8 5z"/></svg>Leo@fenathletics.co.uk</p>
      <p class="contact__row"><svg viewBox="0 0 24 24" aria-hidden="true"><circle cx="12" cy="12" r="10"/></svg>www.fenathletics.co.uk</p>
      <p class="contact__address">Mill Yard, Aldbeck, Thornfield, TF4 2QX</p>
    </div>
  </section>

  <section class="card card--back" aria-label="Business card back">
    <div class="wordmark">Fen Athletics<span class="wordmark__tag">PERFORMANCE WEAR</span></div>
    <div class="brands">
      <span class="brand brand--fen">Fen</span>
      <span class="brand brand--tava"><span class="brand__dot"></span>TavaPuni</span>
      <span class="brand brand--elm"><span class="brand__square"></span>ElmStretch</span>
      <span class="brand brand--grit">Grit and Rain</span>
    </div>
  </section>
</main>
</body>
</html>
```